Fitness Equipment & Service

I want to make the card eye catching and fun. We are called Corvane Motion Limited and we are based in Wales. We sell, install and service all types of fitness equipment from Skipping ropes, right through the Dumbbells, Kettle bells and Barbells through to state of the art Treadmills, Running Machines and Strength Equipment. We also design and install changing room furniture and lockers.

TYPOGRAPHY
We would like to use Futrura. Futura has an appearance of efficiency and forwardness. The typeface is derived
from simple geometric forms (near-perfect circles, triangles and squares) and is based on strokes of
near-even weight, which are low in contrast. This is most visible in the almost perfectly round stroke of
the o, which is nonetheless slightly ovoid.
The lowercase has tall ascenders, which rise above the cap line. The uppercase
characters present proportions similar to those of classical Roman capitals.

TYPOGRAPHIC CONSIDERATIONS
No Strike though
No Horizontal Scaling
No Drop Shadows
No Effects
Never use less than 120% Leading

OUR CORPORATE COLOURS
BRAND GUIDELINES
We were thinking that our primary colour palette consists of the Acid Green (Pantone 382) and Process Black.

We work closely with tquarly Ltd and would like to include their name on the card somewhere. I have attached images of the other brands that we work with as an idea or the small icons I have included that illustrate what we do?. I have very kindly been given permission to use any of the images off the files that I have included below, so I hope these help. I will include these below. I would be open to suggestions if it made the card more striking Can you do it?
Updates

Hi All, Just wanted to add a few thoughts but you are the guys with the creative visions (thats why are here) We are based in Wales, UK and we would be open to lots of different ideas on a theme but must be eye catching, Bold and FUN. If you can or think that the Welsh or any dragon could be put in there then go for it (its not a must have) We have also added some ideas for colour but again its over to you!! GO FOR IT ! Thanks and look forward to your visions! Owen

Hi All, Just thought I would sen through the contact details that need to be on the card. (if you want to play around with icons instead of the wording twitter, Facebook, go for it): Corvane Motion Limited Owen Pritchard Managing Director Mob: +44 (0)7582 913 406 e-mail: sales@corvanemotion.co.uk Web: Corvanemotion.co.uk twitter: @motionLetterbin Facebook: Corvane Motion Limited

```html
<!DOCTYPE html>
<html lang="en">
<head>
<meta charset="utf-8">
<title>Corvane Motion Limited – Business Card</title>
<link rel="stylesheet" href="https://fonts.googleapis.com/css2?family=Arimo:wght@400;700&family=Playfair+Display:wght@600&display=swap">
<style>
  :root {
    --canvas: #e8e6e1;
    --gold-light: #c9a944;
    --gold: #b08f2a;
    --gold-deep: #96781c;
    --navy: #25388a;
    --navy-deep: #1b2a6b;
    --paper: #ffffff;
    --ink: #111111;
    --blue-1: #1f5fa8;
    --blue-2: #16477f;
    --blue-3: #3a86cc;
    --blue-4: #0f2b55;
    --mist: #b7c7d4;
    --sky: #49a6dd;
  }
  * { margin: 0; padding: 0; box-sizing: border-box; }
  html, body {
    width: 1200px; height: 892px; overflow: hidden;
    background: var(--canvas);
  }
  .card {
    position: absolute; left: 290px;
    width: 620px; height: 388px;
    overflow: hidden;
    box-shadow: 0 2px 10px rgba(0,0,0,.18);
  }
  .card--front { top: 40px; background: linear-gradient(160deg, var(--gold-light) 0%, var(--gold) 45%, var(--gold-deep) 100%); }
  .card--back { top: 464px; }

  .name-band {
    position: absolute; left: 262px; top: 0; right: 0; height: 100px;
    background: var(--paper);
    border-bottom: 3px solid var(--ink);
  }
  .brand-disc {
    position: absolute; left: 200px; top: 14px;
    width: 112px; height: 112px; border-radius: 50%;
    background: var(--navy);
    border: 6px solid var(--paper);
  }
  .brand-name {
    position: absolute; left: 40px; top: 140px;
    font: 700 21px/1.3 "Arimo", sans-serif;
    color: var(--navy-deep);
  }
  .person {
    position: absolute; right: 30px; top: 16px; text-align: right;
  }
  .person__name {
    font: 600 31px/1.25 "Playfair Display", serif;
    color: var(--navy);
    white-space: nowrap;
  }
  .person__role {
    font: 400 18px/1.3 "Arimo", sans-serif;
    color: var(--ink);
  }
  .contact {
    position: absolute; right: 28px; top: 176px;
    list-style: none; text-align: right;
  }
  .contact__item {
    display: flex; justify-content: flex-end; align-items: center; gap: 10px;
    font: 400 18px/1.6 "Arimo", sans-serif;
    color: var(--paper);
  }
  .contact__icon {
    width: 16px; height: 16px; flex: none;
    background: var(--navy-deep);
    display: block;
  }

  .back-art { position: absolute; inset: 0; width: 620px; height: 388px; }
  .back-name {
    position: absolute; left: 250px; top: 150px; width: 340px;
    font: 700 40px/1.2 "Arimo", sans-serif;
    color: var(--paper);
    text-align: center;
  }
</style>
</head>
<body>

<section class="card card--front" aria-label="Business card, front">
  <div class="name-band"></div>
  <div class="brand-disc"></div>
  <div class="brand-name">Corvane Motion Limited</div>

  <div class="person">
    <p class="person__name">Owen Pritchard</p>
    <p class="person__role">Managing Director</p>
  </div>

  <ul class="contact">
    <li class="contact__item">+44 (0)7582 913 406
      <svg class="contact__icon" viewBox="0 0 16 16" aria-hidden="true">
        <rect width="16" height="16" fill="#1b2a6b"/>
        <path d="M5 3.5 L7 5.5 L6 7 Q7.5 9 9 10 L10.5 9 L12.5 11 L11 12.5 Q7 12 3.5 5 Z" fill="#fff"/>
      </svg>
    </li>
    <li class="contact__item">sales@corvanemotion.co.uk
      <svg class="contact__icon" viewBox="0 0 16 16" aria-hidden="true">
        <rect width="16" height="16" fill="#1b2a6b"/>
        <rect x="3" y="4.5" width="10" height="7" fill="none" stroke="#fff" stroke-width="1.2"/>
        <path d="M3 4.5 L8 8.5 L13 4.5" fill="none" stroke="#fff" stroke-width="1.2"/>
      </svg>
    </li>
    <li class="contact__item">Corvanemotion.co.uk
      <svg class="contact__icon" viewBox="0 0 16 16" aria-hidden="true">
        <rect width="16" height="16" fill="#1b2a6b"/>
        <circle cx="8" cy="8" r="4.5" fill="none" stroke="#fff" stroke-width="1.2"/>
        <path d="M3.5 8 H12.5" stroke="#fff" stroke-width="1"/>
      </svg>
    </li>
    <li class="contact__item">Corvane Motion Limited<span class="contact__icon"></span></li>
    <li class="contact__item">@motionLetterbin<span class="contact__icon"></span></li>
  </ul>
</section>

<section class="card card--back" aria-label="Business card, back">
  <svg class="back-art" viewBox="0 0 620 388" aria-hidden="false">
    <rect width="620" height="388" fill="#1f5fa8"/>
    <g class="tiles">
      <rect x="0"   y="0"   width="124" height="130" fill="#49a6dd"/>
      <rect x="124" y="0"   width="124" height="130" fill="#16477f"/>
      <rect x="248" y="0"   width="124" height="130" fill="#3a86cc"/>
      <rect x="372" y="0"   width="124" height="130" fill="#0f2b55"/>
      <rect x="496" y="0"   width="124" height="130" fill="#1f5fa8"/>
      <rect x="0"   y="130" width="124" height="129" fill="#16477f"/>
      <rect x="124" y="130" width="124" height="129" fill="#1f5fa8"/>
      <rect x="248" y="130" width="124" height="129" fill="#0f2b55"/>
      <rect x="372" y="130" width="124" height="129" fill="#3a86cc"/>
      <rect x="496" y="130" width="124" height="129" fill="#16477f"/>
      <rect x="0"   y="259" width="124" height="129" fill="#1f5fa8"/>
      <rect x="124" y="259" width="124" height="129" fill="#b7c7d4"/>
      <rect x="248" y="259" width="124" height="129" fill="#1f5fa8"/>
      <rect x="372" y="259" width="124" height="129" fill="#16477f"/>
      <rect x="496" y="259" width="124" height="129" fill="#0f2b55"/>
    </g>
    <g role="img" aria-label="Locker icon">
      <rect x="282" y="30" width="56" height="70" fill="#5a98d3"/>
    </g>
    <g role="img" aria-label="Juice and apple icon">
      <rect x="158" y="164" width="56" height="60" fill="#3b7bc0"/>
    </g>
    <g role="img" aria-label="Bathroom scale icon">
      <rect x="158" y="292" width="56" height="62" fill="#d3dde6"/>
    </g>
    <g role="img" aria-label="Boxing gloves icon">
      <rect x="408" y="292" width="56" height="62" fill="#3b6ba6"/>
    </g>
    <circle cx="40" cy="150" r="150" fill="#25388a" stroke="#ffffff" stroke-width="10"/>
  </svg>
  <p class="back-name">Corvane Motion</p>
</section>

</body>
</html>
```